RQV Wellness Co Business Card for food and Beverage Wizards & Alchemists

One main business card design for a wellness enterprise which represents two brands. We need one primary card design, for two different employees. The only difference between the cards will be the name, title and phone number for each employee, all other design elements will be same.
I've uploaded the logos for each brand. I have also uploaded a mockup which I made using Google's drawing tool. I can provide example images of business cards we find attractive if you would like some help picturing what we like.
I'm picturing the color splash on the back of the card below the two logos to be a dark burgundy or blue. This may sound a bit silly but the feel of the card and color should look almost like wizard dress robes. Dark emerald green, dark blue and dark burgundy with black undertones and gold lace.

Reason: Thank you all for the submissions. I will need some extra time to give you feedback. Cheers

Target Market(s)

Healthy food and beverage industry

Industry/Entity Type

Health And Wellness

Contact Information for Business Card

On one side we would like the business name, location, title of employee, employee name and contact details. On the flip side we would like our two brand logos and a splash of color. We would like the card to have a black font with some gold accents if possible. We would also like the trim of the business card or a middle ply within the card stock to have a color other than white.

Font styles to use
Serif

Colors
ec1f27
0255a3
00a990

Requirements
Must have
• Bold dark colors, happy to provide sample photos of business cards I like from snapgallery. Must have a version for two different employees. Must be sharp, modern and chic.
Nice to have
• Thick card stock layer in between the front and back of card that is either black or gold lace or something to make it feel, well let's say to make it feel expensive.
Should not have
• Should not have any cartoon-ey elements. All business.

```html
<!DOCTYPE html>
<html lang="en">
<head>
<meta charset="utf-8">
<title>RQV Wellness Co – Business Card</title>
<link href="https://fonts.googleapis.com/css2?family=Source+Sans+3:wght@400;600&display=swap" rel="stylesheet">
<style>
  :root {
    --backdrop: #555555;
    --card-black: #000000;
    --card-white: #f8f8f8;
    --text-light: #ffffff;
    --gold: #e5ab00;
    --burgundy: #5e0019;
    --band-black: #0d0d0d;
    --ink: #111111;
  }
  html, body {
    margin: 0;
    padding: 0;
    width: 1200px;
    height: 900px;
    overflow: hidden;
    background: var(--backdrop);
    font-family: "Source Sans 3", sans-serif;
  }
  .stage {
    position: relative;
    width: 1200px;
    height: 900px;
  }
  .card {
    position: absolute;
    top: 170px;
    width: 347px;
    height: 561px;
    overflow: hidden;
  }
  .card-front {
    left: 259px;
    background: var(--card-black);
    color: var(--text-light);
    text-align: center;
  }
  .card-back {
    left: 631px;
    background: var(--card-white);
  }
  .company {
    position: absolute;
    top: 67px;
    left: 0;
    right: 0;
  }
  .company-name {
    margin: 0;
    font-size: 22px;
    font-weight: 600;
    line-height: 28px;
  }
  .company-location {
    margin: 0;
    font-size: 18px;
    line-height: 24px;
  }
  .person {
    position: absolute;
    top: 333px;
    left: 0;
    right: 0;
  }
  .person-name {
    margin: 0;
    color: var(--gold);
    font-size: 24px;
    font-weight: 600;
    line-height: 30px;
  }
  .person-title {
    margin: 0;
    font-size: 18px;
    line-height: 24px;
  }
  .contact-icons {
    position: absolute;
    top: 421px;
    left: 0;
    right: 0;
    display: flex;
    justify-content: center;
    gap: 6px;
  }
  .contact-icons svg { display: block; }
  .contact-details {
    position: absolute;
    top: 457px;
    left: 0;
    right: 0;
    font-size: 18px;
    line-height: 25px;
  }
  .contact-details p { margin: 0; }
  .brand-mark {
    position: absolute;
    left: 0;
    right: 0;
    text-align: center;
    color: var(--ink);
    font-size: 22px;
    font-weight: 600;
  }
  .brand-primary { top: 110px; }
  .brand-secondary { top: 250px; }
  .brand-secondary::before {
    content: "";
    display: block;
    width: 14px;
    height: 14px;
    margin: 0 auto 10px;
    border-radius: 50%;
    background: var(--ink);
  }
  .color-splash {
    position: absolute;
    left: 0;
    bottom: 0;
    display: block;
  }
</style>
</head>
<body>
<main class="stage">
  <section class="card card-front" aria-label="Card front">
    <header class="company">
      <p class="company-name">RQV Wellness Co</p>
      <p class="company-location">Glenbrook,CA</p>
    </header>
    <div class="person">
      <p class="person-name">Miles Carver</p>
      <p class="person-title">Beverage Alchemist</p>
    </div>
    <div class="contact-icons">
      <svg width="26" height="26" viewBox="0 0 26 26" aria-label="Phone">
        <circle cx="13" cy="13" r="13" fill="var(--gold)"/>
        <path d="M9.2 7.2c.5-.4 1.2-.3 1.5.2l1.1 1.8c.3.5.2 1.1-.2 1.4l-.8.6c.6 1.5 1.8 2.8 3.3 3.5l.6-.8c.4-.4 1-.5 1.4-.2l1.8 1.1c.5.3.6 1 .2 1.5l-.8.9c-.6.6-1.5.8-2.3.5-3.2-1.2-5.7-3.7-6.9-6.9-.3-.8-.1-1.7.5-2.3z" fill="#000"/>
      </svg>
      <svg width="26" height="26" viewBox="0 0 26 26" aria-label="Email">
        <circle cx="13" cy="13" r="13" fill="var(--gold)"/>
        <rect x="7" y="8.5" width="12" height="9" rx="1" fill="#000"/>
        <path d="M7.6 9.2 13 13.4l5.4-4.2" fill="none" stroke="var(--gold)" stroke-width="1.1"/>
      </svg>
    </div>
    <div class="contact-details">
      <p>415.555.0142</p>
      <p>rqvwellnessco@mail.com</p>
    </div>
  </section>

  <section class="card card-back" aria-label="Card back">
    <p class="brand-mark brand-primary">RQV Wellness Co</p>
    <p class="brand-mark brand-secondary">Oakvale Provisions</p>
    <svg class="color-splash" width="347" height="561" viewBox="0 0 347 561" aria-hidden="true">
      <path d="M0 455 C80 482 140 478 210 432 S300 345 347 335 L347 561 L0 561Z" fill="var(--burgundy)"/>
      <path d="M0 502 C80 528 140 524 210 478 S300 392 347 383 L347 561 L0 561Z" fill="var(--band-black)"/>
      <path d="M0 542 C80 566 140 562 210 518 S300 432 347 423 L347 561 L0 561Z" fill="var(--gold)"/>
    </svg>
  </section>
</main>
</body>
</html>
```